Website Design Request - Management Consulting Firm

We need a Website designed for an IT Management Staffing and Recruiting firm called TRAVENOK based in San Francisco.

The firm is an high-end technology staffing agency. Our focus is on quality and high-caliber candidates rather than quantity.

The website will have two main home pages. One for the recruiter and another on for the candidates.

The website needs to optimize for mobile devices as well.

I have attached few mock-ups that I have done just to show what I am thinking. The UI needs to be very clean, fluid, and it needs to have a modern, rustic, professional feel to it.

Target Market(s)

Technology Manager, Director, VP, CIO of Companies that have $4b-10b dollar revenue. Such as larkspurdwellings.example , https://www.velmorian.example/, quillnet.example, zib.example

Industry/Entity Type

Management Consulting

Number of Pages Required

5+ page

Font styles to use
Sans Serif

Colors
f37122
ffffff

Requirements
Must have
• Please review mock-ups for suggestions
Nice to have
Should not have

```html
<!DOCTYPE html>
<html lang="en">
<head>
<meta charset="utf-8">
<title>TRAVENOK – IT Project Management Staffing</title>
<link href="https://fonts.googleapis.com/css2?family=Open+Sans:wght@400;600;700&display=swap" rel="stylesheet">
<style>
:root{
  --orange:#f37122;
  --orange-dark:#d9531a;
  --orange-light:#f9955a;
  --ink:#2b2b2b;
  --muted:#777;
  --line:#d8d8d8;
  --hero-bg:#ecebe9;
  --band-bg:#efefef;
  --white:#fff;
  --dark:#333;
}
*{box-sizing:border-box;margin:0;padding:0}
html,body{width:692px;height:1200px;overflow:hidden;background:var(--white)}
body{font-family:"Open Sans",Arial,sans-serif;color:var(--ink);position:relative}
.site-header{position:absolute;top:0;left:0;width:692px;height:46px;display:flex;align-items:center;padding:0 46px;background:var(--white)}
.brand{font-weight:700;font-size:22px;color:var(--orange);letter-spacing:1px}
.main-nav{margin-left:auto;display:flex;align-items:center;gap:14px;font-size:10px;font-weight:600}
.btn-sign-up,.btn-sign-in{padding:5px 10px;color:var(--white);font-size:9px}
.btn-sign-up{background:var(--orange)}
.btn-sign-in{background:var(--dark)}
.hero{position:absolute;top:46px;left:0;width:692px;height:364px;background:var(--hero-bg);overflow:hidden}
.hero-photo{position:absolute;top:0;right:0;width:420px;height:364px;background:linear-gradient(90deg,rgba(236,235,233,1) 0%,#d9d4cf 30%,#bfb5ad 60%,#8e8279 100%)}
.hero-copy{position:absolute;left:72px;top:74px;width:250px}
.hero-title{font-size:15px;font-weight:700;line-height:1.25;text-transform:uppercase}
.hero-sub{font-size:9px;color:#555;margin-top:8px;line-height:1.4}
.signup-form{display:flex;margin-top:12px}
.signup-form .email-field{width:148px;height:26px;background:var(--white);border:1px solid var(--line);font-size:8px;color:#999;padding:7px 8px}
.signup-form .btn-offers{height:26px;background:var(--orange);color:var(--white);font-size:8px;font-weight:600;padding:8px 10px}
.hero-note{font-size:6px;color:#888;margin-top:6px}
.employer-cta{position:absolute;left:72px;top:264px}
.employer-cta h2{font-size:15px;font-weight:600}
.employer-cta a{font-size:7px;color:#555;text-decoration:underline}
.slider-dots{position:absolute;left:330px;top:348px;display:flex;gap:4px}
.slider-dots span{width:5px;height:5px;border-radius:50%;background:#bbb}
.slider-dots span.active{background:var(--orange)}
.tab-band{position:absolute;top:410px;left:0;width:692px;height:34px;background:var(--orange);display:flex;padding-left:46px}
.tab{font-size:12px;font-weight:600;padding:9px 22px;color:var(--white)}
.tab.active{background:var(--white);color:var(--ink);border-top:3px solid var(--orange)}
.steps-heading{position:absolute;top:480px;left:0;width:692px;text-align:center}
.steps-kicker{font-size:9px;color:#555}
.steps-title{font-size:14px;font-weight:600;margin-top:6px}
.steps-lines{position:absolute;top:540px;left:0}
.step-circle{position:absolute;width:116px;height:116px;border-radius:50%;display:flex;align-items:center;justify-content:center}
.step-1{left:287px;top:558px;background:var(--orange-dark)}
.step-2{left:287px;top:697px;background:var(--orange)}
.step-3{left:287px;top:839px;background:var(--orange-light)}
.step-text{position:absolute;width:220px}
.step-text h3{font-size:13px;font-weight:600}
.step-text p{font-size:8px;color:#555;margin-top:4px;line-height:1.4}
.step-text.right{left:418px}
.step-text.left{left:56px;text-align:right}
.contact-band{position:absolute;top:990px;left:0;width:692px;height:162px;background:var(--band-bg);text-align:center}
.contact-title{font-size:13px;font-weight:700;margin-top:40px}
.contact-blurb{font-size:7px;color:#888;width:380px;margin:10px auto 0;line-height:1.5}
.contact-details{display:flex;justify-content:center;gap:70px;margin-top:18px;font-size:11px}
.contact-item{display:flex;align-items:center;gap:10px}
.contact-icon{width:26px;height:26px;border-radius:50%;background:var(--white);display:flex;align-items:center;justify-content:center}
.site-footer{position:absolute;top:1152px;left:0;width:692px;height:48px;display:flex;align-items:center;padding:0 46px;font-size:7px;color:#888}
.social-links{display:flex;gap:10px}
.social-links span{width:8px;height:8px;background:#999}
.copyright{margin-left:auto}
</style>
</head>
<body>
<header class="site-header">
  <div class="brand">TRAVENOK</div>
  <nav class="main-nav">
    <span>Professionals</span>
    <span>Employers</span>
    <span class="btn-sign-up">Sign Up</span>
    <span class="btn-sign-in">Sign In</span>
  </nav>
</header>

<section class="hero">
  <div class="hero-photo" role="img" aria-label="Photo of a smiling businesswoman holding a clipboard, with a colleague working at a laptop in a bright office"></div>
  <div class="hero-copy">
    <h1 class="hero-title">Looking for IT Project<br>Management Jobs?</h1>
    <p class="hero-sub">Upload your resume, accept interview requests, get offers</p>
    <div class="signup-form">
      <div class="email-field">Your Email Address</div>
      <div class="btn-offers">Get Offers Now</div>
    </div>
    <p class="hero-note">By entering your email you agree to our terms and privacy policy</p>
  </div>
  <div class="employer-cta">
    <h2>Looking for talents?</h2>
    <a>See how it works for Employers</a>
  </div>
  <div class="slider-dots"><span class="active"></span><span></span><span></span></div>
</section>

<nav class="tab-band">
  <span class="tab active">How it works?</span>
  <span class="tab">Why us</span>
</nav>

<section class="steps">
  <div class="steps-heading">
    <p class="steps-kicker">3 - simple steps</p>
    <h2 class="steps-title">Employers pay 25% more for a better FIT Project Manager</h2>
  </div>
  <svg class="steps-lines" width="692" height="420" viewBox="0 0 692 420">
    <path d="M403 76 C470 110 470 190 403 214" fill="none" stroke="#ccc" stroke-width="1.5"/>
    <path d="M287 216 C225 250 225 330 287 356" fill="none" stroke="#ccc" stroke-width="1.5"/>
  </svg>

  <div class="step-circle step-1">
    <svg width="30" height="30" viewBox="0 0 30 30"><path d="M15 4 L8 12 H12 V19 H18 V12 H22 Z" fill="#fff"/><rect x="5" y="22" width="20" height="4" fill="#fff"/></svg>
  </div>
  <div class="step-text right" style="top:596px">
    <h3>Upload your resume</h3>
    <p>Answer few questions and upload your resume.</p>
  </div>

  <div class="step-circle step-2">
    <svg width="26" height="30" viewBox="0 0 26 30"><path d="M3 2 H17 L23 8 V28 H3 Z" fill="none" stroke="#fff" stroke-width="2.5"/><path d="M8 14 H18 M8 19 H18 M8 24 H15" stroke="#fff" stroke-width="2"/></svg>
  </div>
  <div class="step-text left" style="top:732px">
    <h3>We Send You Interview Requests</h3>
    <p>Interested to someone? With a single click send interview request and let us handle the rest.</p>
  </div>

  <div class="step-circle step-3">
    <svg width="30" height="30" viewBox="0 0 30 30"><path d="M5 15 L12 22 L25 8" fill="none" stroke="#fff" stroke-width="4"/></svg>
  </div>
  <div class="step-text right" style="top:876px">
    <h3>Get $1000 Bonus</h3>
    <p>Find a job and get $1000 bonus TRAVENOK</p>
  </div>
</section>

<section class="contact-band">
  <h2 class="contact-title">INTERESTED? CONTACT US!</h2>
  <p class="contact-blurb">Tell us about the role you need to fill and our team will reply within one business day with a shortlist of vetted project managers ready to talk.</p>
  <div class="contact-details">
    <div class="contact-item">
      <span class="contact-icon"><svg width="12" height="12" viewBox="0 0 12 12"><path d="M3 1 L5 3.5 L4 5 C5 7 6 8 7.5 8.5 L9 7.5 L11 9.5 L9.5 11 C5 11 1 7 1 2.5 Z" fill="#333"/></svg></span>
      <span>08-555 014 27</span>
    </div>
    <div class="contact-item">
      <span class="contact-icon"><svg width="12" height="10" viewBox="0 0 12 10"><rect x="0.5" y="0.5" width="11" height="9" fill="#333"/><path d="M1 1 L6 5.5 L11 1" fill="none" stroke="#fff"/></svg></span>
      <span>info@travenok.example</span>
    </div>
  </div>
</section>

<footer class="site-footer">
  <div class="social-links"><span></span><span></span><span></span><span></span></div>
  <div class="copyright">Your career partner. All rights reserved</div>
</footer>
</body>
</html>
```